Thornbury Building Company - Card Design

I am looking to use the logo designs that you already did for me to develop a business card. I would like the card to have a black background and be double sided. I want white and green logo and text. I have attached an inspiration photo of a look that I like. I would like to use the Vertical Logo attached to take up the full front side of the card. On the back where I have my name and information, I would like to have the horizontal logo or maybe even just the image of the 'A' and trees without the text. I am open, but I am looking for something clean and simple and I want the green to really pop! Additional files can be found under Design #: 58302946

Target Market(s)

Homeowners

Industry/Entity Type

Construction

Contact Information for Business Card

Name: Marcus Thornbury, Title: Project Manager, Phone: 555.274.8136, Email: thornburybuildingcompany@mailvesta.com, address: 487 Larkspur Ln, Ashgrove, NV 95033, Lic# 2468317

Colors
00AB8E
00BBA5
67D7C9
C6EFE9
E9F9F6

Requirements
Nice to have
• I would like to see the logos that I have already got from ArtLoomHub, though I am open to new ones

```html
<!DOCTYPE html>
<html lang="en">
<head>
<meta charset="utf-8">
<title>Thornbury Building Company – Business Cards</title>
<link rel="stylesheet" href="https://fonts.googleapis.com/css2?family=Oswald:wght@300;400;500;600&family=Michroma&display=swap">
<style>
  :root {
    --backdrop: #dadada;
    --card: #0e1419;
    --green: #66ff1f;
    --white: #ffffff;
    --muted: #e8e8e8;
  }
  * { margin: 0; padding: 0; box-sizing: border-box; }
  html, body {
    width: 1200px; height: 846px; overflow: hidden;
    background: var(--backdrop);
    font-family: "Oswald", sans-serif;
  }
  .canvas { position: relative; width: 1200px; height: 846px; }
  .card {
    position: absolute; left: 347px; width: 509px; height: 291px;
    background: var(--card);
  }
  .card--back { top: 99px; }
  .card--front { top: 457px; }

  /* Back: identity column */
  .brand-block {
    position: absolute; left: 60px; top: 96px; width: 143px;
    display: flex; flex-direction: column; align-items: center; gap: 8px;
  }
  .brand-square { width: 30px; height: 30px; background: var(--green); }
  .brand-name {
    color: var(--white); font-weight: 500; font-size: 13px;
    line-height: 1.15; letter-spacing: 0.06em; text-align: center; text-transform: uppercase;
  }
  .person-name {
    position: absolute; left: 58px; top: 174px; width: 150px;
    color: var(--green); font-weight: 600; font-size: 17.5px;
    letter-spacing: 0.01em; text-transform: uppercase; white-space: nowrap;
  }
  .person-role {
    position: absolute; left: 59px; top: 200px;
    color: var(--muted); font-weight: 300; font-style: italic; font-size: 11.5px;
    letter-spacing: 0.03em; white-space: nowrap;
  }
  .contact-list {
    position: absolute; left: 225px; top: 154px; list-style: none;
  }
  .contact-item {
    display: flex; align-items: center; height: 22px;
    color: var(--white); font-weight: 300; font-size: 14.5px; letter-spacing: 0.02em;
    white-space: nowrap;
  }
  .contact-icon { width: 18px; height: 16px; margin-right: 8px; fill: var(--green); flex: none; }

  /* Front: centred lockup */
  .front-square {
    position: absolute; left: 224px; top: 70px; width: 62px; height: 62px;
    background: var(--green);
  }
  .est {
    position: absolute; top: 117px; width: 52px;
    font-family: "Michroma", sans-serif; font-size: 9px; letter-spacing: 0.22em;
    color: var(--white); text-align: center;
  }
  .est::before, .est::after {
    content: ""; position: absolute; left: 4px; right: 4px; height: 1px; background: var(--green);
  }
  .est::before { top: -4px; }
  .est::after { bottom: -5px; }
  .est--left { left: 109px; }
  .est--right { left: 346px; }
  .front-name {
    position: absolute; left: 0; right: 0; top: 160px;
    color: var(--white); font-weight: 500; font-size: 27px;
    letter-spacing: 0.08em; text-align: center; text-transform: uppercase;
  }
</style>
</head>
<body>
<main class="canvas">

  <section class="card card--back" aria-label="Business card, contact side">
    <div class="brand-block">
      <span class="brand-square"></span>
      <span class="brand-name">Thornbury<br>Building Company</span>
    </div>
    <p class="person-name">Marcus Thornbury</p>
    <p class="person-role">Project Manager / Lic# 2468317</p>
    <ul class="contact-list">
      <li class="contact-item">
        <svg class="contact-icon" viewBox="0 0 24 24" aria-hidden="true"><path d="M6.6 10.8a15.1 15.1 0 0 0 6.6 6.6l2.2-2.2c.3-.3.7-.4 1-.2 1.1.4 2.3.6 3.6.6.6 0 1 .4 1 1V20c0 .6-.4 1-1 1A17 17 0 0 1 3 4c0-.6.4-1 1-1h3.5c.6 0 1 .4 1 1 0 1.3.2 2.5.6 3.6.1.3 0 .7-.2 1z"/><path d="M14 3a7 7 0 0 1 7 7h-1.6A5.4 5.4 0 0 0 14 4.6zm0 3a4 4 0 0 1 4 4h-1.6A2.4 2.4 0 0 0 14 7.6z"/></svg>
        555.274.8136
      </li>
      <li class="contact-item">
        <svg class="contact-icon" viewBox="0 0 24 18" aria-hidden="true"><path d="M1 1h22v16H1zm2 2v.4l9 6.6 9-6.6V3zm0 2.9V15h4.5l3-3.4L3 5.9zm18 0-7.5 5.7 3 3.4H21z"/></svg>
        thornburybuildingcompany@mailvesta.com
      </li>
      <li class="contact-item">
        <svg class="contact-icon" viewBox="0 0 24 22" aria-hidden="true"><path d="M12 1 1 11h3v10h6v-6h4v6h6V11h3l-4-3.6V3h-3v1.7z"/></svg>
        487 Larkspur Ln, Ashgrove, NV 95033
      </li>
    </ul>
  </section>

  <section class="card card--front" aria-label="Business card, brand side">
    <span class="front-square"></span>
    <span class="est est--left">ESTD</span>
    <span class="est est--right">2020</span>
    <p class="front-name">Thornbury Building Company</p>
  </section>

</main>
</body>
</html>
```